Redesign of business card for Cedar Ridge Mechanical

We are looking for a new design for our business cards for Cedar Ridge Mechanical. We are a plumbing & HVAC construction company, operating on the West Coast of Canada and USA. Logo attached.
Industry/Entity Type
Construction - Plumbing & HVAC
Contact Information for Business Card
Name, address, phone numbers, email, website address
Look and feel
Each slider illustrates characteristics of the customer's brand and the style your logo design should communicate.

```html
<!DOCTYPE html>
<html lang="en">
<head>
<meta charset="utf-8">
<title>Cedar Ridge Mechanical – Business Cards</title>
<link href="https://fonts.googleapis.com/css2?family=Montserrat:wght@400;600;700&display=swap" rel="stylesheet">
<style>
  :root {
    --backdrop: #6e6e6e;
    --card-white: #ffffff;
    --ink: #000000;
    --accent-grey: #8a8a8a;
    --text-light: #ffffff;
  }
  * { box-sizing: border-box; margin: 0; padding: 0; }
  html, body {
    width: 1200px; height: 780px; overflow: hidden;
    background: var(--backdrop);
    font-family: "Montserrat", sans-serif;
  }
  .stage {
    width: 1200px; height: 780px;
    display: flex; align-items: center; justify-content: center; gap: 40px;
  }
  .card {
    position: relative;
    width: 520px; height: 300px;
    background: var(--card-white);
    overflow: hidden;
  }
  .card-back .swoosh { position: absolute; inset: 0; }
  .contact {
    position: absolute; left: 28px; top: 30px;
    color: var(--text-light);
  }
  .contact-name { font-weight: 700; font-size: 20px; letter-spacing: 0.5px; }
  .contact-title { font-weight: 400; font-size: 12px; margin: 2px 0 14px; }
  .contact-list { list-style: none; font-size: 13px; line-height: 22px; }
  .contact-list li { display: flex; align-items: center; gap: 8px; }
  .contact-list svg { width: 12px; height: 12px; fill: var(--text-light); flex: none; }
  .address {
    position: absolute; right: 26px; bottom: 12px;
    color: var(--text-light); font-size: 13px; line-height: 18px; text-align: left;
  }
  .brand {
    position: absolute; display: flex; align-items: center;
    color: var(--ink); font-weight: 700; text-transform: uppercase;
  }
  .brand-mark { background: var(--ink); flex: none; }
  .card-back .brand {
    right: 40px; top: 64px; flex-direction: column; gap: 10px;
    font-size: 18px; line-height: 24px; letter-spacing: 0.5px; text-align: center;
  }
  .card-back .brand-mark { width: 18px; height: 18px; }
  .card-front .brand {
    left: 0; right: 0; top: 0; bottom: 0; justify-content: center;
    gap: 16px; font-size: 28px; letter-spacing: 1px;
  }
  .card-front .brand-mark { width: 28px; height: 28px; }
</style>
</head>
<body>
<main class="stage">
  <section class="card card-back">
    <svg class="swoosh" viewBox="0 0 520 300" preserveAspectRatio="none" aria-hidden="true">
      <path d="M0,0 L264,0 C304,90 296,182 396,222 C450,238 495,238 520,234 L520,300 L0,300 Z" fill="var(--accent-grey)"/>
      <path d="M0,0 L250,0 C290,90 280,190 380,232 C440,250 490,252 520,248 L520,300 L0,300 Z" fill="var(--ink)"/>
    </svg>
    <div class="contact">
      <p class="contact-name">DANIEL MARSH</p>
      <p class="contact-title">Managing Director</p>
      <ul class="contact-list">
        <li><svg viewBox="0 0 24 24"><path d="M6.6 10.8a15 15 0 0 0 6.6 6.6l2.2-2.2a1 1 0 0 1 1-.25 11.4 11.4 0 0 0 3.6.6 1 1 0 0 1 1 1V20a1 1 0 0 1-1 1A17 17 0 0 1 3 4a1 1 0 0 1 1-1h3.5a1 1 0 0 1 1 1c0 1.25.2 2.45.6 3.6a1 1 0 0 1-.25 1z"/></svg>6045550142</li>
        <li><svg viewBox="0 0 24 24"><path d="M7 1h10a2 2 0 0 1 2 2v18a2 2 0 0 1-2 2H7a2 2 0 0 1-2-2V3a2 2 0 0 1 2-2zm0 3v14h10V4z"/></svg>60455501870</li>
        <li><svg viewBox="0 0 24 24"><path d="M2 5h20v14H2zm2 2v.5l8 5 8-5V7zm0 2.8V17h16V9.8l-8 5z"/></svg>info@cedarridgemech.com</li>
        <li><svg viewBox="0 0 24 24"><path d="M12 2a10 10 0 1 0 0 20 10 10 0 0 0 0-20zm-1 17.9A8 8 0 0 1 4.1 11H7c.1 3 1.5 6.4 4 8.9zM7 9H4.3A8 8 0 0 1 11 4.1C8.6 6.5 7.2 8 7 9zm6 10.9c2.5-2.5 3.9-5.9 4-8.9h2.9a8 8 0 0 1-6.9 8.9zM17 9c-.2-1-1.6-2.5-4-4.9A8 8 0 0 1 19.7 9zM9 11h6c-.1 2.6-1.2 5.2-3 7.2-1.8-2-2.9-4.6-3-7.2zm0-2c.3-1.4 1.4-3 3-4.7 1.6 1.7 2.7 3.3 3 4.7z"/></svg>www.cedarridgemech.com</li>
      </ul>
    </div>
    <div class="brand"><span class="brand-mark"></span><span>Cedar Ridge<br>Mechanical</span></div>
    <p class="address">Your address, City<br>State, Zip 1234</p>
  </section>

  <section class="card card-front">
    <div class="brand"><span class="brand-mark"></span>Cedar Ridge Mechanical</div>
  </section>
</main>
</body>
</html>
```